KLV Plant Services

We are a heavy diesel mechanical business with additional air con certificates, remapping engine rebuilt

Contact Information for Business Card

Company Name, Director Name, Managing Director, Contact details, email and website

Font styles to use
Serif
Script

```html
<!DOCTYPE html>
<html lang="en">
<head>
<meta charset="utf-8">
<title>KLV Plant Services – Business Card</title>
<link href="https://fonts.googleapis.com/css2?family=Libre+Baskerville:wght@400;700&family=Great+Vibes&display=swap" rel="stylesheet">
<style>
  :root {
    --navy: #05056b;
    --navy-ink: #1a1a7a;
    --silver: #c9ccd3;
    --paper: #ffffff;
    --text: #2a2a2a;
    --backdrop: #3a3a3c;
  }
  * { margin: 0; padding: 0; box-sizing: border-box; }
  html, body { width: 1200px; height: 875px; overflow: hidden; }
  body {
    background: var(--backdrop);
    font-family: "Libre Baskerville", Georgia, serif;
    display: flex;
    align-items: center;
    justify-content: center;
    gap: 40px;
  }
  .card {
    position: relative;
    width: 560px;
    height: 320px;
    border-radius: 18px;
    overflow: hidden;
  }
  /* Front */
  .card-front {
    background: var(--navy);
    display: flex;
    align-items: center;
    justify-content: center;
  }
  .wordmark {
    display: flex;
    align-items: center;
    gap: 14px;
    font-weight: 700;
  }
  .wordmark .mark-circle {
    border-radius: 50%;
    flex: none;
  }
  .card-front .wordmark { color: var(--silver); font-size: 34px; }
  .card-front .mark-circle { width: 54px; height: 54px; border: 3px solid var(--silver); }

  /* Back */
  .card-back { background: var(--paper); color: var(--text); }
  .card-back .wordmark {
    position: absolute; top: 36px; right: 34px;
    color: var(--navy-ink); font-size: 20px;
  }
  .card-back .mark-circle { width: 34px; height: 34px; border: 2px solid var(--navy-ink); }
  .rule { position: absolute; height: 1.5px; background: var(--navy-ink); }
  .rule-main { top: 112px; left: 200px; right: 28px; }
  .rule-name { top: 214px; left: 28px; width: 200px; }

  .company-block {
    position: absolute; top: 124px; right: 34px;
    text-align: right; font-size: 11px; line-height: 1.6;
  }
  .company-name { color: var(--navy-ink); text-transform: uppercase; font-size: 11.5px; }

  .person { position: absolute; left: 30px; top: 138px; }
  .person-name {
    font-family: "Great Vibes", cursive;
    color: var(--navy-ink); font-size: 40px; line-height: 1;
  }
  .person-title { font-size: 12px; margin-top: 2px; }

  .contacts {
    position: absolute; left: 30px; top: 226px;
    list-style: none; font-size: 12px; line-height: 1.7;
  }
  .contacts li { display: flex; align-items: center; gap: 10px; }
  .contacts svg { width: 12px; height: 12px; fill: var(--navy-ink); flex: none; }
</style>
</head>
<body>
  <section class="card card-front" aria-label="Business card front">
    <div class="wordmark">
      <span class="mark-circle"></span>
      <span class="wordmark-text">KLV Plant Services</span>
    </div>
  </section>

  <section class="card card-back" aria-label="Business card back">
    <div class="wordmark">
      <span class="mark-circle"></span>
      <span class="wordmark-text">KLV Plant Services</span>
    </div>
    <div class="rule rule-main"></div>

    <div class="company-block">
      <div class="company-name">KLV Plant Services</div>
      <div>18 Forge Road, Millbrook, State</div>
      <div>Country, Zip Code 01235</div>
      <div>www.KLVPlant.example</div>
    </div>

    <div class="person">
      <div class="person-name">Daniel Hartley</div>
      <div class="person-title">Managing Director</div>
    </div>
    <div class="rule rule-name"></div>

    <ul class="contacts">
      <li>
        <svg viewBox="0 0 24 24" aria-hidden="true"><path d="M6.6 10.8a15 15 0 0 0 6.6 6.6l2.2-2.2a1 1 0 0 1 1-.25 11.4 11.4 0 0 0 3.6.57 1 1 0 0 1 1 1V20a1 1 0 0 1-1 1A17 17 0 0 1 3 4a1 1 0 0 1 1-1h3.5a1 1 0 0 1 1 1c0 1.25.2 2.45.57 3.57a1 1 0 0 1-.25 1z"/></svg>
        (555) 210-3974
      </li>
      <li>
        <svg viewBox="0 0 24 24" aria-hidden="true"><path d="M7 1h10a2 2 0 0 1 2 2v18a2 2 0 0 1-2 2H7a2 2 0 0 1-2-2V3a2 2 0 0 1 2-2zm0 4v13h10V5zm5 14.5a1 1 0 1 0 0 2 1 1 0 0 0 0-2z"/></svg>
        (555) 210-3974
      </li>
      <li>
        <svg viewBox="0 0 24 24" aria-hidden="true"><path d="M6 2h12v5H6zM4 8h16a2 2 0 0 1 2 2v7h-4v5H6v-5H2v-7a2 2 0 0 1 2-2zm4 7v5h8v-5z"/></svg>
        (555) 210-3974
      </li>
      <li>
        <svg viewBox="0 0 24 24" aria-hidden="true"><path d="M2 5h20v14H2zm2 2v.5l8 5 8-5V7z"/></svg>
        info@klvplant.example
      </li>
    </ul>
  </section>
</body>
</html>
```